Wedding filmmaker needs artistic business card design - brightwaterreels.ca

We are high end wedding filmmakers in a major market who produce cinematic wedding films. We require a business card design that communicates our quality, artistry, and professionalism yet looks progressive and friendly. Colors and design should skew appeal more to the bride-to-be who is usually the decision maker but not be overtly feminine per se. This means generally light pastel shades of ivory, purple, pink, yellow, as examples.
We already have a name logo established: the words "Brightwater Reels" in the font Great Vibes. Designs must use Kraft natural cardstock as the print stock and am leaning heavily toward our name logo in white, but I am open to black as well. Please design any color elements with spot white underneath where possible.
Do not try to compliment or take inspiration from our website design. Treat the card design as a separate stand alone.
Thank you so much for your hard work!

Target Market(s)

Affluent couples spending $50,000+ on their wedding

Industry/Entity Type

Progressive

Contact Information for Business Card

Peter Brightwater
Producer
905-482-7139
www.brightwaterreels.ca
peter@brightwaterreels.ca
twitter @brightwater287

Font styles to use
Serif
Sans Serif

Requirements
Must have
• - Brightwater Reels name logo (reference GIF uploaded for reference only) and catch phrase: Breathtaking wedding films (I'm open to capitalizing all three words, or just first, or all in small caps). I favor logo, and catch phrase on front of card and my contact details on the other side but if you feel strongly about a different design, go for it!
• - Design must be submitted shown on Kraft natural cardstock NOT WHITE cardstock, If you're not familiar with Kraft, this is what it looks like: http://www.quillandlatchjournal.com/wp-content/uploads/2013/07/il_570xN.382745196_kq3m.jpg
Nice to have
• - An original graphic element (eg. movie reel, bouquet, confetti, etc.) that compliments the name logo but is subtle and discreet, doesn't overpower or entangle it.
• -Great use of balance, composition, negative space, etc. I like clean tasteful design
Should not have
• -Lousy boring clip art.
• -Graphic elements, fonts, or color palette from our website
• -White cardstock background
• -designs you have previously submitted for other contests
• -Bold dark colors (eg. red, orange navy blue, etc.)
• -High tech futuristic designs like you'd create for a software company

```html
<!DOCTYPE html>
<html lang="en">
<head>
<meta charset="utf-8">
<title>Brightwater Reels – Business Card</title>
<link rel="stylesheet" href="https://fonts.googleapis.com/css2?family=Exo+2:wght@400;500&display=swap">
<style>
  :root {
    --backdrop: #e4e2e6;
    --kraft-light: #d2b48f;
    --kraft: #c5a47c;
    --kraft-deep: #b8956b;
    --band-mauve: #b7a2c6;
    --band-blush: #e3c1cc;
    --spot-white: #ffffff;
    --ink-brown: #4b3626;
  }
  * { margin: 0; padding: 0; box-sizing: border-box; }
  html, body {
    width: 1200px;
    height: 840px;
    overflow: hidden;
    background: var(--backdrop);
    font-family: "Exo 2", Arial, sans-serif;
  }
  .canvas {
    width: 1200px;
    height: 840px;
    display: flex;
    align-items: center;
    justify-content: center;
  }
  .business-card {
    position: relative;
    width: 1000px;
    height: 572px;
    background: radial-gradient(ellipse at 55% 60%, var(--kraft-light) 0%, var(--kraft) 55%, var(--kraft-deep) 100%);
    box-shadow: 0 10px 30px rgba(60, 45, 30, 0.2);
    overflow: hidden;
  }
  .wave-art {
    position: absolute;
    inset: 0;
    width: 100%;
    height: 100%;
  }
  .wave-band { fill: var(--band-mauve); }
  .wave-highlight { fill: var(--band-blush); }
  .wave-line { fill: none; stroke: var(--spot-white); stroke-width: 4; }

  .holder-identity {
    position: absolute;
    top: 40px;
    right: 36px;
    text-align: right;
    color: var(--spot-white);
  }
  .holder-name {
    font-size: 34px;
    font-weight: 500;
    letter-spacing: 2px;
    text-transform: uppercase;
    line-height: 1.1;
  }
  .holder-title {
    font-size: 24px;
    font-weight: 400;
    letter-spacing: 1px;
    margin-top: 4px;
  }

  .brand-name {
    position: absolute;
    top: 262px;
    right: 40px;
    font-size: 44px;
    font-weight: 400;
    letter-spacing: 1px;
    color: var(--spot-white);
  }
  .tagline {
    position: absolute;
    top: 352px;
    right: 40px;
    text-align: right;
    font-size: 22px;
    font-weight: 500;
    letter-spacing: 3px;
    font-variant: small-caps;
    color: var(--ink-brown);
  }

  .contact-list {
    position: absolute;
    left: 52px;
    bottom: 22px;
    list-style: none;
    color: var(--ink-brown);
    font-size: 19px;
    letter-spacing: 1px;
  }
  .contact-item {
    display: flex;
    align-items: center;
    gap: 12px;
    height: 29px;
  }
  .contact-icon {
    width: 18px;
    height: 18px;
    fill: var(--ink-brown);
    flex: none;
  }
</style>
</head>
<body>
<main class="canvas">
  <section class="business-card" aria-label="Brightwater Reels business card">
    <svg class="wave-art" viewBox="0 0 1000 572" preserveAspectRatio="none" aria-hidden="true">
      <path class="wave-band" d="M0 0 H1000 V200 C880 240 760 232 640 205 C520 178 400 160 300 180 C180 205 80 300 0 470 Z"/>
      <path class="wave-highlight" d="M560 236 C700 232 860 215 1000 178 V198 C870 238 720 246 560 236 Z"/>
      <path class="wave-line" d="M12 418 C70 300 170 215 320 186"/>
    </svg>

    <header class="holder-identity">
      <h1 class="holder-name">Peter Brightwater</h1>
      <p class="holder-title">Producer</p>
    </header>

    <p class="brand-name">Brightwater Reels</p>
    <p class="tagline">Breathtaking Wedding Films</p>

    <ul class="contact-list">
      <li class="contact-item">
        <svg class="contact-icon" viewBox="0 0 24 24" aria-hidden="true"><path d="M6.6 10.8a15.1 15.1 0 0 0 6.6 6.6l2.2-2.2c.3-.3.7-.4 1-.2 1.1.4 2.3.6 3.6.6.6 0 1 .4 1 1V20c0 .6-.4 1-1 1C10.6 21 3 13.4 3 4c0-.6.4-1 1-1h3.5c.6 0 1 .4 1 1 0 1.3.2 2.5.6 3.6.1.3 0 .7-.2 1z"/></svg>
        <span>905-482-7139</span>
      </li>
      <li class="contact-item">
        <svg class="contact-icon" viewBox="0 0 24 24" aria-hidden="true"><path d="M2 5h20v14H2zm2 2v.5l8 5 8-5V7zm0 2.8V17h16V9.8l-8 5z"/></svg>
        <span>peter@brightwaterreels.ca</span>
      </li>
      <li class="contact-item">
        <svg class="contact-icon" viewBox="0 0 24 24" aria-hidden="true"><path d="M12 2a10 10 0 1 0 0 20 10 10 0 0 0 0-20zm6.9 6h-3a15 15 0 0 0-1.3-3.9A8 8 0 0 1 18.9 8zM12 4c.8 1.2 1.5 2.5 1.9 4h-3.8c.4-1.5 1.1-2.8 1.9-4zM4.3 14a8 8 0 0 1 0-4h3.4a16 16 0 0 0 0 4zm.8 2h3a15 15 0 0 0 1.3 3.9A8 8 0 0 1 5.1 16zm3-8h-3a8 8 0 0 1 4.3-3.9A15 15 0 0 0 8.1 8zM12 20c-.8-1.2-1.5-2.5-1.9-4h3.8c-.4 1.5-1.1 2.8-1.9 4zm2.3-6H9.7a14 14 0 0 1 0-4h4.6a14 14 0 0 1 0 4zm.3 5.9a15 15 0 0 0 1.3-3.9h3a8 8 0 0 1-4.3 3.9zm1.7-5.9a16 16 0 0 0 0-4h3.4a8 8 0 0 1 0 4z"/></svg>
        <span>www.brightwaterreels.ca</span>
      </li>
      <li class="contact-item">
        <svg class="contact-icon" viewBox="0 0 24 24" aria-hidden="true"><circle cx="12" cy="12" r="8"/></svg>
        <span>@brightwater287</span>
      </li>
    </ul>
  </section>
</main>
</body>
</html>
```